Small legal and financial translation company needs Squarespace website, brochure and logo

Hello,
We are Lumarin Services (www.lumarinservices-example.com), a boutique legal and financial translation company. We offer our services mainly to Spanish customers. Our primary line of business is the translation of financial statements, but we translate a wide variety legal and financial texts.
The project we are offering comprises three parts: a redo of the current website, an informational brochure for potential customer and a logo design. These three parts should provide a consistent image. We would develop content soon.
We are looking for a website that would look like a typical law firm website, nothing too fancy. Right now, it is in English, Spanish and French, although the new site need only be in English and Spanish. There must be good toggling between the English and Spanish versions. There would be no need for tie-ins to social media and it would not contain a blog. Basically, a static site. We aren't interesting in driving traffic to the site or SEO, as we will contact nearly all potential customers beforehand. The website must be built in Squarespace to enable a smooth transition. The content would be similar to the current page, we'll be working on the exact content, but a rough draft is attached.
The brochure will be some three pages and would introduce the company to potential customers, using similar images as the website and the logo to be designed.
The only specifications for the logo is, as the website and brochure, it convey a sense of security and trust.
Feel free to ask with any questions as this is the first time we have used this platform.
Thank you!
Updates

I've added a more or less final version for the text in the brochure and updated the brief. Added Wednesday, June 10, 2015

Target Market(s)

Spanish law firms, auditors, accountants, banks, investment firms

Industry/Entity Type

Finance

Logo Text

Lumarin Services

Number of Pages Required

5+ page

Font styles to use
Serif

Requirements
Must have
• The website must be built in Squarespace and have a good option to toggle between English and Spanish versions.
• Brochure must be in both English and Spanish, I'm attaching a rough draft of the information that it will probably have. This should give an idea about what to include and the spacing. I will update it to include the final information.
Nice to have
• Would be nice to have some quality finance- and legal-related images
Should not have
• Vibrant colours

```html
<!DOCTYPE html>
<html lang="en">
<head>
<meta charset="utf-8">
<title>Lumarin Services – Pricing</title>
<link rel="stylesheet" href="https://fonts.googleapis.com/css2?family=Montserrat:wght@700&family=Oswald:wght@400;500&family=Cormorant+Garamond:wght@500&family=Crimson+Text&display=swap">
<style>
  :root {
    --teal: #2b9c98;
    --brand: #a9d8ee;
    --white: #ffffff;
    --page-bg: #e6e6e6;
    --nav-grey: #8c8c8c;
    --body-text: #4a4a4a;
    --footer-top: #2f2f2f;
    --footer-bottom: #1f1f1f;
    --hero-dark: #2c2c2c;
    --hero-mid: #6f6f6f;
    --hero-light: #a8a8a8;
  }
  * { margin: 0; padding: 0; box-sizing: border-box; }
  html, body { width: 1200px; height: 981px; overflow: hidden; }
  body { position: relative; background: var(--page-bg); font-family: "Crimson Text", serif; }

  .hero {
    position: absolute; left: 0; top: 0; width: 1200px; height: 446px;
    background:
      radial-gradient(ellipse 260px 300px at 560px 300px, var(--hero-light), transparent 70%),
      linear-gradient(90deg, var(--hero-mid) 0%, var(--hero-dark) 22%, var(--hero-mid) 45%, var(--hero-light) 52%, var(--hero-dark) 70%, var(--hero-mid) 100%);
  }
  .brand {
    position: absolute; left: 16px; top: 30px;
    font-family: "Cormorant Garamond", serif; font-weight: 500;
    font-size: 34px; line-height: 1; color: var(--brand);
  }
  .top-nav {
    position: absolute; right: 14px; top: 56px; display: flex; gap: 26px;
  }
  .top-nav a {
    font-family: "Montserrat", sans-serif; font-weight: 700; font-size: 12.5px;
    letter-spacing: 0.06em; color: var(--white); text-decoration: none;
  }
  .hero-title {
    position: absolute; left: 0; width: 1200px; top: 198px; text-align: center;
    font-family: "Montserrat", sans-serif; font-weight: 700; font-size: 58px;
    letter-spacing: 0.03em; color: var(--white);
  }

  .side-nav { position: absolute; left: 181px; top: 528px; }
  .side-nav .lang {
    font-family: "Cormorant Garamond", serif; font-size: 21px; color: var(--teal); margin-bottom: 4px;
  }
  .side-nav ul { list-style: none; }
  .side-nav li {
    font-family: "Oswald", sans-serif; font-weight: 500; font-size: 15px;
    letter-spacing: 0.12em; line-height: 32.6px; color: var(--nav-grey);
  }
  .side-nav li.current { color: var(--teal); }

  .content { position: absolute; left: 404px; top: 528px; width: 610px; }
  .content h1 {
    font-family: "Cormorant Garamond", serif; font-weight: 500; font-size: 33px;
    color: var(--teal); line-height: 1.2; margin-bottom: 17px;
  }
  .content p {
    font-size: 17.5px; line-height: 21px; letter-spacing: 0.045em; color: var(--body-text);
  }

  .footer-top { position: absolute; left: 0; top: 876px; width: 1200px; height: 56px; background: var(--footer-top); }
  .footer-bottom { position: absolute; left: 0; top: 932px; width: 1200px; height: 49px; background: var(--footer-bottom); }
</style>
</head>
<body>
  <header class="hero" role="img" aria-label="Black and white photograph of a steep city street lined with stone buildings under a cloudy sky">
    <div class="brand">Lumarin Services</div>
    <nav class="top-nav">
      <a href="#">HOME</a>
      <a href="#">ENGLISH</a>
      <a href="#">SPANISH</a>
    </nav>
    <div class="hero-title">PRICING</div>
  </header>

  <nav class="side-nav">
    <div class="lang">English</div>
    <ul>
      <li>WHO WE ARE</li>
      <li>BENEFITS</li>
      <li>LEGAL TRANSLATION</li>
      <li>FINANCIAL TRANSLATION</li>
      <li>TRANSLATION SPECIALIST</li>
      <li class="current">PRICING</li>
      <li>CONTACT</li>
    </ul>
  </nav>

  <main class="content">
    <h1>Pricing</h1>
    <p>Our prices take into account a wide variety of factors based on each individual job to be carried out. Urgency, formatting, past experience, technical complexity and many other factors go into preparing a quote tailored to customers' needs. We are always happy to discuss pricing with our customers, although a basic starting point for any job stands around EUR 0.085/word.</p>
  </main>

  <footer>
    <div class="footer-top"></div>
    <div class="footer-bottom"></div>
  </footer>
</body>
</html>
```